Harbourline Builders Business Card Design

We need a business card for an established builder of high quality bespoke homes in Auckland and Northland. We build and renovate homes collaboratively facilitating effective communication between owners, builders, architects, suppliers and tradespeople. We have never built or renovated a home that leaks or has faults. We only use reliable materials. We have never been sued or had legal action taken against us. We are honest builders of bespoke homes not group mass produced homes. Our niche market is in character homes. We practice sustainability and have built a lot of coastal property. We have been in business for over thirty years . We would like to see natural colors of the environment sand,sea and maybe vegetation . The design should communicate quality, sustainability,fair pricing, open communication and the originality of bespoke building. And the fact that the builder is registered.

Industry/Entity Type

Business

Contact Information for Business Card

Rowan Tellick Builders
Ph. 021583917
18 Kestrel Rd Harwood Bay Auckland 0814
PO Box 927 Mangawhai 0583

```html
<!DOCTYPE html>
<html lang="en">
<head>
<meta charset="utf-8">
<title>Harbourline Builders – Business Card</title>
<link rel="stylesheet" href="https://fonts.googleapis.com/css2?family=Source+Sans+3:wght@400;600;700&display=swap">
<style>
  :root {
    --backdrop-top: #2a2a2a;
    --backdrop-bottom: #050505;
    --sand-light: #f6efe0;
    --sea-deep: #2d6a70;
    --sea-text: #25585d;
    --vegetation: #3f5a3c;
    --body-text: #3a3a34;
    --reverse-text: #f3e8d2;
  }
  * { margin: 0; padding: 0; box-sizing: border-box; }
  html, body {
    width: 1200px;
    height: 900px;
    overflow: hidden;
  }
  body {
    position: relative;
    background: linear-gradient(to bottom, var(--backdrop-top), var(--backdrop-bottom));
    font-family: "Source Sans 3", "Myriad Pro", Arial, sans-serif;
  }
  .card {
    position: absolute;
    top: 306px;
    width: 440px;
    height: 271px;
    border-radius: 11px;
  }
  .card--front {
    left: 149px;
    background: var(--sand-light);
  }
  .card--back {
    left: 608px;
    background: var(--sea-deep);
  }
  .wordmark {
    position: absolute;
    font-weight: 700;
    white-space: nowrap;
    letter-spacing: -0.3px;
  }
  .card--front .wordmark {
    left: 37px;
    top: 82px;
    font-size: 33px;
    color: var(--vegetation);
  }
  .card--back .wordmark {
    right: 33px;
    top: 206px;
    font-size: 27px;
    color: var(--reverse-text);
  }
  .contact {
    position: absolute;
    left: 186px;
    top: 139px;
    color: var(--body-text);
    font-size: 12.5px;
    line-height: 16px;
  }
  .contact__name {
    color: var(--sea-text);
    font-size: 15.5px;
    font-weight: 600;
    margin-bottom: 10px;
  }
  .contact__phone {
    display: flex;
    align-items: center;
    gap: 7px;
    margin-bottom: 7px;
  }
  .contact__phone svg {
    width: 10px;
    height: 10px;
    fill: var(--sea-deep);
  }
</style>
</head>
<body>
  <section class="card card--front" aria-label="Card front">
    <div class="wordmark">Harbourline Builders</div>
    <div class="contact">
      <p class="contact__name">Rowan Tellick Builders</p>
      <p class="contact__phone">
        <svg viewBox="0 0 24 24" aria-hidden="true"><path d="M6.6 10.8c1.4 2.8 3.8 5.1 6.6 6.6l2.2-2.2c.3-.3.7-.4 1-.2 1.1.4 2.3.6 3.6.6.6 0 1 .4 1 1V20c0 .6-.4 1-1 1C10.6 21 3 13.4 3 4c0-.6.4-1 1-1h3.5c.6 0 1 .4 1 1 0 1.3.2 2.5.6 3.6.1.3 0 .7-.2 1l-2.3 2.2z"/></svg>
        <span>021583917</span>
      </p>
      <p>18 Kestrel Rd Harwood Bay</p>
      <p>Auckland 0814</p>
      <p>PO Box 927 Mangawhai 0583</p>
    </div>
  </section>

  <section class="card card--back" aria-label="Card back">
    <div class="wordmark">Harbourline Builders</div>
  </section>
</body>
</html>
```